Stationary Suite for Aussie Law Firm

We are a small law firm operating out of Albany, Western Australia. We have a logo, which we love and was the winner of a ArtworkHive contest last year.
We require a suite of business stationary products incorporating our logo and contact details. These should be:
1. Letterhead (A4)
The letterhead should incorporate the following information in addition to the logo:
ABN 38 602 917 255 (this is our Australian Business Number)
Beatrix Lund atf The BJL Legal Trust t/as Harbour Gate Legal & Conveyancing (legal name of the business)
Address: Wexley House, Wexley Street, Albany
Postal Address: PO Box 8147, Albany WA 6332
Telephone: 0491 670 382
Facsimile: 08 9722 5913
Email: info@harbourgatelegal.com.au
Website: www.harbourgatelegal.com.au
2. Business Card (90mm x 55mm)
I've attached my current business card layout just for your information.
The front of the business card should include the following information in addition to the logo:
Beatrix Lund
Director & Principal Solicitor
Telephone: 0491 670 382
Facsimile: 08 9722 5913
Email: beatrix@harbourgatelegal.com.au
The back of the card should be similar to the back of my existing card, but should only have the logo in white and the address of our website (www.harbourgatelegal.com.au)
3. Email signature block
This should include the same information as the front of the business card.
4. With Compliments slip (DL size)
The With Compliments slip should include the same information as the Letterhead.
5. Banner (830mm x 2000mm)
We need a banner designed for use at marketing events. This should include our website details and logo - other than that you have fairly free reign with the design.
6. Flyer (DL)
We need a flyer setting out our services and main contact details for use at marketing events. The details to be included are:
Telephone: 0491 670 382
Web: www.harbourgatelegal.com.au
Areas of law:
Wills & Estate Planning
Probate & Letters of Administration
Property Law & Conveyancing
General Commercial Law
Business Law
Style guide:
Please look at our website for an idea as to the style of designs we are looking for - www.harbourgatelegal.com.au. The design should be modern, sharp and professional.
Colours:
The CMYK details for the colours in our logo are:
Light Blue C72 M5 Y0 K0
Dark Blue C97 M72 Y16 K30
Edit 31/7/2014
I have added a couple of photos that we have used on our website, and additional photos. These are from our local area, so feel free to use these in your designs or to inform them.
- Calibri, Century Gothic

```html
<!DOCTYPE html>
<html lang="en">
<head>
<meta charset="utf-8">
<title>Harbour Gate Legal &amp; Conveyancing – Stationery Suite</title>
<link rel="stylesheet" href="https://fonts.googleapis.com/css2?family=Questrial&family=Roboto+Condensed:wght@400;700&family=Arimo:wght@400&display=swap">
<style>
:root{
  --navy:#0d3a6b;
  --sky:#3aa7e0;
  --grey:#6d6d6d;
  --paper:#ffffff;
  --backdrop:#4a3526;
}
*{margin:0;padding:0;box-sizing:border-box}
html,body{width:1200px;height:1000px;overflow:hidden}
body{background:var(--backdrop);position:relative;font-family:"Roboto Condensed",sans-serif;color:var(--grey)}
address{font-style:normal}
.sheet{position:absolute;background:var(--paper);box-shadow:0 4px 14px rgba(0,0,0,.45)}
.brand{font-family:"Questrial",sans-serif;text-align:center;line-height:1.15;letter-spacing:.5px;white-space:nowrap}
.brand .name{display:block}
.brand .sub{display:block;font-size:.55em;letter-spacing:2px}

/* Letterhead */
.letterhead{left:75px;top:65px;width:440px;height:617px}
.letterhead .brand-block{position:absolute;left:0;top:17px;width:147px;height:59px;background:var(--navy);display:flex;align-items:center;justify-content:center}
.letterhead .brand{color:#fff;font-size:11px}
.letterhead .web{position:absolute;left:22px;top:78px;font-family:Arimo,sans-serif;font-size:9px;color:var(--navy)}
.letterhead .contact{position:absolute;right:20px;top:22px;text-align:right;font-family:"Roboto Condensed",sans-serif;font-size:8.5px;line-height:11.6px;color:var(--grey)}
.letterhead .legal{position:absolute;left:0;right:0;top:575px;text-align:center;font-family:Arimo,sans-serif;font-size:8px;line-height:12px}

/* Business card front */
.card-front{left:637px;top:68px;width:403px;height:251px}
.card-front .brand{position:absolute;left:30px;top:70px;width:130px;color:var(--sky);font-size:15px}
.card-front .brand .sub{letter-spacing:1.2px}
.card-front .divider{position:absolute;left:168px;top:42px;width:2px;height:166px;background:var(--navy)}
.person{position:absolute}
.person .who{font-size:22px;color:var(--navy);line-height:1}
.person .role{font-size:12px;color:var(--grey);margin-top:2px}
.details{font-size:10px;line-height:12.8px;margin-top:20px}
.details dl{display:grid;grid-template-columns:50px auto}
.details dt{font-weight:700;color:var(--navy)}
.card-front .person{left:188px;top:92px}

/* Business card back */
.card-back{left:637px;top:351px;width:403px;height:253px;background:var(--navy);color:#fff}
.card-back .brand{position:absolute;left:0;right:0;top:118px;font-size:21px;color:#fff}
.card-back .web{position:absolute;left:0;right:0;top:170px;text-align:center;font-family:Arimo,sans-serif;font-size:14px}

/* Email signature */
.signature{left:73px;top:700px;width:502px;height:172px}
.signature .panel{position:absolute;left:0;top:0;width:194px;height:100%;background:var(--navy);display:flex;align-items:center;justify-content:center}
.signature .brand{color:#fff;font-size:15px}
.signature .person{left:235px;top:33px}
.signature .person .who{font-size:20px}
.signature .details{font-size:9px;line-height:11.6px;margin-top:17px}
.signature .details dl{grid-template-columns:42px auto}

/* With compliments slip */
.compliments{left:636px;top:628px;width:504px;height:243px}
.compliments .title{position:absolute;left:31px;top:30px;font-size:28px;font-weight:400;color:var(--navy)}
.compliments .foot{position:absolute;left:31px;top:208px;width:296px;font-family:"Roboto Condensed",sans-serif;font-size:5px;line-height:8px;white-space:nowrap}
.compliments .foot b{color:var(--navy);font-weight:700}
.compliments .foot .gap{display:inline-block;width:6px}
.compliments .panel{position:absolute;right:0;top:0;width:168px;height:100%;background:var(--navy);color:#fff}
.compliments .panel .brand{position:absolute;left:0;right:0;top:64px;font-size:12px;color:#fff}
.compliments .panel .brand .sub{letter-spacing:1.2px}
.compliments .panel .info{position:absolute;left:0;right:0;top:202px;text-align:center;font-family:"Roboto Condensed",sans-serif;font-size:4.4px;line-height:6.5px;white-space:nowrap}
.compliments .panel .info .url{font-family:Arimo,sans-serif;font-size:8px;line-height:10px}

.caption{position:absolute;left:0;right:0;top:880px;text-align:center;font-family:Arimo,sans-serif;font-size:72px;color:#fff;line-height:1}
</style>
</head>
<body>

<section class="sheet letterhead" aria-label="Letterhead">
  <div class="brand-block"><div class="brand"><span class="name">HARBOUR GATE</span><span class="sub">LEGAL &amp; CONVEYANCING</span></div></div>
  <p class="web">www.harbourgatelegal.com.au</p>
  <address class="contact">
    Wexley House, Wexley Street, Albany<br>
    Mail:&nbsp; PO Box 8147, Albany WA 6332<br>
    Telephone:&nbsp; 0491 670 382<br>
    Facsimile:&nbsp; 08 9722 5913<br>
    Email:&nbsp; info@harbourgatelegal.com.au
  </address>
  <p class="legal">Beatrix Lund atf The BJL Legal Trust t/as Harbour Gate Legal &amp; Conveyancing<br>ABN 38 602 917 255</p>
</section>

<section class="sheet card-front" aria-label="Business card front">
  <div class="brand"><span class="name">HARBOUR GATE</span><span class="sub">LEGAL &amp; CONVEYANCING</span></div>
  <div class="divider"></div>
  <div class="person">
    <p class="who">Beatrix Lund</p>
    <p class="role">Director &amp; Principal Solicitor</p>
    <div class="details">
      <p>Wexley House, Wexley Street, Albany</p>
      <dl>
        <dt>Mail:</dt><dd>PO Box 8147, Albany WA 6332</dd>
        <dt>Telephone:</dt><dd>0491 670 382</dd>
        <dt>Facsimile:</dt><dd>08 9722 5913</dd>
        <dt>Email:</dt><dd>beatrix@harbourgatelegal.com.au</dd>
      </dl>
    </div>
  </div>
</section>

<section class="sheet card-back" aria-label="Business card back">
  <div class="brand"><span class="name">HARBOUR GATE</span><span class="sub">LEGAL &amp; CONVEYANCING</span></div>
  <p class="web">www.harbourgatelegal.com.au</p>
</section>

<section class="sheet signature" aria-label="Email signature">
  <div class="panel"><div class="brand"><span class="name">HARBOUR GATE</span><span class="sub">LEGAL &amp; CONVEYANCING</span></div></div>
  <div class="person">
    <p class="who">Beatrix Lund</p>
    <p class="role">Director &amp; Principal Solicitor</p>
    <div class="details">
      <p>Wexley House, Wexley Street, Albany</p>
      <dl>
        <dt>Mail:</dt><dd>PO Box 8147, Albany WA 6332</dd>
        <dt>Telephone:</dt><dd>0491 670 382</dd>
        <dt>Facsimile:</dt><dd>08 9722 5913</dd>
        <dt>Email:</dt><dd>beatrix@harbourgatelegal.com.au</dd>
      </dl>
    </div>
  </div>
</section>

<section class="sheet compliments" aria-label="With compliments slip">
  <h2 class="title">With Compliments</h2>
  <p class="foot">Wexley House, Wexley Street, Albany<br>
    <b>Mail:</b> PO Box 8147, Albany WA 6332<span class="gap"></span><b>Telephone:</b> 0491 670 382<span class="gap"></span><b>Facsimile:</b> 08 9722 5913<span class="gap"></span><b>Email:</b> info@harbourgatelegal.com.au</p>
  <div class="panel">
    <div class="brand"><span class="name">HARBOUR GATE</span><span class="sub">LEGAL &amp; CONVEYANCING</span></div>
    <p class="info"><span class="url">www.harbourgatelegal.com.au</span><br>Beatrix Lund atf The BJL Legal Trust t/as Harbour Gate Legal &amp; Conveyancing<br>ABN 38 602 917 255</p>
  </div>
</section>

<p class="caption">Stationary</p>

</body>
</html>
```